e-commerce store for sport clothing online store "baseball merchandise "web application...

I want to design a UX/UI for my web application website for the online store I will provide you with the following:
1. screen shots of the initial design for the pages>
2. the logo files.
3. The brand guideline file.

the provided files (screen shots) is guideline I want to see CREATIVITY with the UX/UI DESIGN.
PS. PLEASE FOLLOW THE BRANDGUIDE LINE CAREFULLY SPECIALLY THE TYPOGRAPHY & THE COLOR CODES.

PLEASE VISIT THIS WEBSITE brightlane.varomi-qz.com to see more for the screens.

```html
<!DOCTYPE html>
<html lang="en">
<head>
<meta charset="UTF-8">
<title>Product Detail</title>
<link href="https://fonts.googleapis.com/css2?family=Titillium+Web:wght@400;600;700&family=Lato:wght@400;700&display=swap" rel="stylesheet">
<style>
  :root {
    --navy: #0f2147;
    --red: #b8123b;
    --badge: #d3143a;
    --ink: #111111;
    --text: #222222;
    --rule: #cfcfcf;
    --btn-grey: #9a9a9a;
    --white: #ffffff;
    --tee: #7fe6c6;
  }
  * { margin: 0; padding: 0; box-sizing: border-box; }
  html, body { width: 1200px; height: 3263px; overflow: hidden; background: var(--white); }
  .screen {
    position: relative; width: 360px; height: 979px;
    transform: scale(3.33334); transform-origin: 0 0;
    font-family: "Lato", sans-serif; color: var(--text);
  }
  .app-bar { position: absolute; left: 0; top: 0; width: 360px; height: 80px; background: var(--navy); }
  .app-bar__title {
    position: absolute; left: 0; right: 0; top: 29px; text-align: center;
    font-family: "Titillium Web", sans-serif; font-weight: 700; font-size: 16px; color: var(--white);
  }
  .app-bar__back { position: absolute; left: 22px; top: 30px; }
  .app-bar__cart { position: absolute; left: 311px; top: 28px; }
  .cart-badge {
    position: absolute; left: 326px; top: 20px; width: 16px; height: 16px; border-radius: 50%;
    background: var(--badge); border: 1.5px solid var(--white); color: var(--white);
    font-size: 9px; font-weight: 700; line-height: 13px; text-align: center;
  }
  .gallery {
    position: absolute; left: 20px; top: 120px; width: 321px; height: 246px;
    border-radius: 8px; background: var(--white); box-shadow: 0 1px 5px rgba(0,0,0,.25); overflow: hidden;
  }
  .gallery__photo {
    position: absolute; left: 75px; top: 0; width: 171px; height: 246px;
    background: linear-gradient(180deg, #c79a83 0%, var(--tee) 12%, #74dcbc 70%, #6a4d8a 86%, #3b3150 100%);
  }
  .gallery-dots { position: absolute; left: 165px; top: 379px; display: flex; gap: 3px; }
  .gallery-dots span { width: 8px; height: 8px; border-radius: 50%; border: 1.2px solid var(--navy); }
  .gallery-dots span.is-active { background: var(--navy); }
  .product-name {
    position: absolute; left: 20px; top: 406px;
    font-family: "Titillium Web", sans-serif; font-weight: 700; font-size: 20px; color: var(--ink);
  }
  .product-price {
    position: absolute; left: 20px; top: 437px;
    font-family: "Titillium Web", sans-serif; font-weight: 700; font-size: 18px; color: var(--red);
  }
  .rule { position: absolute; left: 20px; width: 328px; height: 1px; background: var(--rule); }
  .option-label { position: absolute; left: 20px; font-size: 15px; color: var(--ink); }
  .swatch {
    position: absolute; left: 20px; top: 530px; width: 48px; height: 42px; border-radius: 5px;
    border: 1px solid var(--navy); padding: 2px;
  }
  .swatch__photo { width: 100%; height: 100%; border-radius: 3px; background: linear-gradient(180deg, var(--tee) 0%, #77d9bb 70%, #5c4a7e 100%); }
  .size-chip {
    position: absolute; top: 640px; width: 23px; height: 23px; border-radius: 50%;
    border: 1.2px solid var(--navy); font-size: 12px; line-height: 21px; text-align: center; color: var(--navy);
  }
  .size-chip.is-selected { background: var(--navy); color: var(--white); }
  .qty-row { position: absolute; left: 20px; top: 714px; height: 22px; display: flex; align-items: center; gap: 5px; }
  .qty-btn {
    width: 22px; height: 22px; border-radius: 50%; border: 1.2px solid #555;
    font-size: 14px; line-height: 19px; text-align: center; color: #555;
  }
  .qty-btn--plus { background: #4a5574; border-color: #4a5574; color: var(--white); }
  .qty-value { width: 20px; height: 20px; border: 1px solid #888; font-size: 12px; text-align: center; line-height: 18px; }
  .stock-note { margin-left: 10px; color: var(--red); font-size: 14px; }
  .cart-panel {
    position: absolute; left: 5px; top: 742px; width: 350px; height: 56px; background: var(--white);
    border-radius: 10px; box-shadow: 0 1px 6px rgba(0,0,0,.3);
  }
  .add-to-cart {
    position: absolute; left: 7px; top: 6px; width: 337px; height: 45px; border-radius: 6px;
    background: var(--btn-grey); color: var(--white); font-weight: 700; font-size: 14px;
    line-height: 45px; text-align: center; letter-spacing: .2px;
  }
  .description-head { position: absolute; left: 20px; top: 803px; font-size: 15px; color: var(--ink); }
  .description-toggle { position: absolute; left: 331px; top: 807px; }
  .description-body { position: absolute; left: 20px; top: 833px; width: 305px; font-size: 13px; line-height: 17px; color: var(--ink); }
  .description-body p + p { margin-top: 20px; }
</style>
</head>
<body>
<div class="screen">
  <header class="app-bar">
    <svg class="app-bar__back" width="20" height="20" viewBox="0 0 20 20"><path d="M18 10H3M10 3L3 10l7 7" fill="none" stroke="#fff" stroke-width="2.2"/></svg>
    <div class="app-bar__title">Product Detail</div>
    <svg class="app-bar__cart" width="26" height="24" viewBox="0 0 26 24"><path d="M1 2h4l4 13h12l3-9H7" fill="none" stroke="#fff" stroke-width="2.4" stroke-linejoin="round"/><path d="M8 8h15l-2.5 6H9.5z" fill="#fff"/><circle cx="10" cy="20.5" r="2.2" fill="#fff"/><circle cx="20" cy="20.5" r="2.2" fill="#fff"/></svg>
    <div class="cart-badge">1</div>
  </header>

  <div class="gallery">
    <div class="gallery__photo" role="img" aria-label="Model wearing a mint short-sleeve graphic tee with patterned purple shorts"></div>
  </div>
  <div class="gallery-dots"><span></span><span class="is-active"></span><span></span></div>

  <h1 class="product-name">Sunny Shore Graphic Tee</h1>
  <div class="product-price">19.000 KD</div>

  <div class="rule" style="top:482px"></div>
  <div class="option-label" style="top:498px">Color:</div>
  <div class="swatch"><div class="swatch__photo" role="img" aria-label="Mint colour option thumbnail"></div></div>

  <div class="rule" style="top:591px"></div>
  <div class="option-label" style="top:606px">Size:</div>
  <div class="size-chip" style="left:20px">S</div>
  <div class="size-chip is-selected" style="left:56px">L</div>

  <div class="rule" style="top:681px"></div>
  <div class="option-label" style="top:689px">Qty:</div>
  <div class="qty-row">
    <div class="qty-btn">−</div>
    <div class="qty-value">0</div>
    <div class="qty-btn qty-btn--plus">+</div>
    <span class="stock-note">Out of Stock</span>
  </div>

  <div class="cart-panel"><div class="add-to-cart">ADD TO CART</div></div>

  <div class="description-head">Description</div>
  <svg class="description-toggle" width="14" height="10" viewBox="0 0 14 10"><path d="M2 8l5-5 5 5" fill="none" stroke="#111" stroke-width="2"/></svg>
  <div class="description-body">
    <p>The name says it all!</p>
    <p>Short Sleeve, Featuring hand drawn artwork with super soft pigment dye.</p>
  </div>
</div>
</body>
</html>
```